Sparrow Haulage needs a business card design.

Design a double-sided business card for new freight business. On the front, would like to see our logo along with the following info:

Martin Obuya
CEO/FOUNDER
555-206-7142
martinobuya@sparrow-haulage.example

On the reverse side, we would like to use the graphic image of our logo only without the Sparrow Haulage name.

```html
<!DOCTYPE html>
<html lang="en">
<head>
<meta charset="utf-8">
<title>Sparrow Haulage — Business Card</title>
<link href="https://fonts.googleapis.com/css2?family=Arimo:wght@400;700&display=swap" rel="stylesheet">
<style>
  :root {
    --backdrop: #e2e2e2;
    --card-white: #f6f6f6;
    --navy: #0a0a5c;
    --red: #c4121c;
    --ink: #2b2b2b;
    --muted: #4a4a4a;
    --white: #ffffff;
  }
  * { box-sizing: border-box; margin: 0; padding: 0; }
  html, body { width: 1200px; height: 930px; overflow: hidden; }
  body {
    background: var(--backdrop);
    font-family: "Arimo", Arial, sans-serif;
    display: flex;
    align-items: center;
    justify-content: center;
    gap: 60px;
  }
  .card {
    width: 525px;
    height: 300px;
    position: relative;
    box-shadow: 0 10px 24px rgba(0,0,0,0.12);
  }
  .card--front { background: var(--card-white); }
  .card--back {
    background: var(--navy);
    display: flex;
    align-items: center;
    justify-content: center;
  }

  /* front: identity block */
  .identity {
    position: absolute;
    left: 30px;
    top: 30px;
  }
  .identity__mark {
    width: 12px; height: 12px;
    background: var(--red);
    margin-bottom: 8px;
  }
  .identity__name {
    font-weight: 700;
    font-size: 17px;
    letter-spacing: 0.5px;
    text-transform: uppercase;
    color: var(--navy);
  }
  .identity__name .surname { color: var(--red); }
  .identity__role {
    font-size: 12px;
    letter-spacing: 0.5px;
    color: var(--muted);
    margin-top: 2px;
  }

  .contacts {
    list-style: none;
    margin-top: 14px;
    font-size: 12px;
    color: var(--ink);
    line-height: 1.45;
  }
  .contacts li { display: flex; align-items: center; gap: 7px; }
  .contacts svg { width: 10px; height: 10px; flex: none; }
  .contacts .web-accent { color: var(--red); }
  .contacts .web-base { color: var(--navy); }

  /* brand wordmark */
  .brand {
    position: absolute;
    right: 40px;
    top: 118px;
    display: flex;
    align-items: center;
    gap: 14px;
  }
  .brand__square { width: 40px; height: 40px; background: var(--red); flex: none; }
  .brand__name {
    font-weight: 700;
    font-size: 24px;
    letter-spacing: 4px;
    text-transform: uppercase;
    color: var(--navy);
    line-height: 1.05;
  }

  /* back: plain brand shape only */
  .back-mark {
    width: 80px;
    height: 80px;
    background: var(--white);
    transform: translate(-10px, -14px);
  }
</style>
</head>
<body>
  <section class="card card--front" aria-label="Card front">
    <div class="identity">
      <div class="identity__mark"></div>
      <p class="identity__name">Martin <span class="surname">Obuya</span></p>
      <p class="identity__role">CEO/FOUNDER</p>
      <ul class="contacts">
        <li>
          <svg viewBox="0 0 10 10" aria-hidden="true"><path d="M2 1 L4 1 L4.6 3 L3.5 3.8 Q4.5 6 6.2 6.6 L7 5.5 L9 6 L9 8 Q8 9 6.5 8.7 Q2 7.5 1.2 3 Q1 1.8 2 1Z" fill="var(--red)"/></svg>
          555-206-7142
        </li>
        <li>
          <svg viewBox="0 0 10 10" aria-hidden="true"><rect x="0.5" y="2" width="9" height="6.5" fill="var(--red)"/><path d="M0.5 2 L5 5.6 L9.5 2" fill="none" stroke="#fff" stroke-width="0.8"/></svg>
          martinobuya@sparrow-haulage.example
        </li>
        <li>
          <svg viewBox="0 0 10 10" aria-hidden="true"><circle cx="5" cy="5" r="4.5" fill="var(--red)"/><path d="M0.5 5 H9.5 M5 0.5 V9.5 M1.5 2.8 H8.5 M1.5 7.2 H8.5" stroke="#fff" stroke-width="0.6"/></svg>
          <span><span class="web-base">www.sparrow-</span><span class="web-accent">haulage</span>.example</span>
        </li>
      </ul>
    </div>
    <div class="brand">
      <span class="brand__square"></span>
      <span class="brand__name">Sparrow<br>Haulage</span>
    </div>
  </section>

  <section class="card card--back" aria-label="Card back">
    <div class="back-mark" aria-hidden="true"></div>
  </section>
</body>
</html>
```